Billboard advertisement design

Health & Fitness centre requires a billboard advertisement design for an allocated space out the front of the shopping centre in which it is located. Copper Ridge Health & Fitness is located in a small town with one other competitor. Looking for a fun, trendy sign to draw people's attention and make sure Copper Ridge is instantly recognisable. Sign location is in the middle of town on the national highway. Approximate size is 12' x 5'. Final design will encourage people who have been thinking about joining the gym to take the first step in leading a fitter and healthier lifestyle.

Target Market(s)

Health conscious members of the community that have been thinking about taking the next step and joining a gym

Industry/Entity Type

Shopping

Requirements
Must have
• Please utilise attached logo
Nice to have
• Contact info is (07) 4958 6301 info@copperridgefitness.com.au

```html
<!DOCTYPE html>
<html lang="en">
<head>
<meta charset="utf-8">
<title>Copper Ridge Health &amp; Fitness – Billboard</title>
<link rel="stylesheet" href="https://fonts.googleapis.com/css2?family=Bebas+Neue&family=Oswald:wght@400&display=swap">
<style>
  :root {
    --page-bg: #e9edf2;
    --board-dark: #4f5459;
    --board-mid: #8a9096;
    --board-light: #a9aeb3;
    --photo-skin: #b98d70;
    --photo-shadow: #3a3a3c;
    --headline: #ffffff;
    --brand-panel: #ffffff;
    --brand-ink: #1f4f9e;
    --contact-ink: #f2f2f2;
  }
  html, body {
    margin: 0;
    padding: 0;
    width: 1200px;
    height: 801px;
    overflow: hidden;
    background: var(--page-bg);
  }
  .billboard {
    position: absolute;
    left: 40px;
    top: 167px;
    width: 1120px;
    height: 467px;
    overflow: hidden;
    background: radial-gradient(ellipse at 40% 45%, var(--board-light) 0%, var(--board-mid) 45%, var(--board-dark) 100%);
    box-shadow: 0 6px 24px rgba(0,0,0,0.18);
  }
  .contact-email {
    position: absolute;
    left: 44px;
    top: 26px;
    margin: 0;
    font-family: "Oswald", sans-serif;
    font-size: 14px;
    letter-spacing: 4px;
    color: var(--contact-ink);
  }
  .athletes-photo {
    position: absolute;
    left: 40px;
    top: 70px;
    width: 560px;
    height: 397px;
    background: linear-gradient(100deg, rgba(58,58,60,0.15) 0%, rgba(185,141,112,0.55) 30%, rgba(58,58,60,0.6) 55%, rgba(185,141,112,0.55) 75%, rgba(58,58,60,0.15) 100%);
    border-radius: 40% 40% 0 0 / 20% 20% 0 0;
  }
  .headline {
    position: absolute;
    left: 680px;
    top: 122px;
    width: 420px;
    margin: 0;
    font-family: "Bebas Neue", sans-serif;
    font-weight: 400;
    color: var(--headline);
    text-align: center;
    line-height: 1;
  }
  .headline-main {
    display: block;
    font-size: 112px;
    letter-spacing: 2px;
  }
  .headline-sub {
    display: block;
    margin-top: 14px;
    font-size: 70px;
    letter-spacing: 1px;
  }
  .brand-panel {
    position: absolute;
    left: 0;
    top: 0;
    width: 1120px;
    height: 467px;
  }
  .brand-name {
    position: absolute;
    left: 745px;
    top: 368px;
    width: 350px;
    margin: 0;
    font-family: "Bebas Neue", sans-serif;
    font-weight: 400;
    color: var(--brand-ink);
    text-align: center;
    line-height: 1;
  }
  .brand-name-main {
    display: block;
    font-size: 50px;
    letter-spacing: 2px;
  }
  .brand-name-tag {
    display: block;
    margin-top: 2px;
    font-size: 16px;
    letter-spacing: 22px;
    padding-left: 22px;
  }
</style>
</head>
<body>
  <section class="billboard" aria-label="Copper Ridge Health &amp; Fitness billboard">
    <p class="contact-email">INFO@COPPERRIDGEFITNESS.COM.AU</p>

    <div class="athletes-photo" role="img" aria-label="Photo of a woman and a man lifting yellow dumbbells"></div>

    <svg class="brand-panel" viewBox="0 0 1120 467" aria-hidden="true">
      <path d="M585 467 C 650 360, 820 318, 1120 330 L 1120 467 Z" fill="var(--brand-panel)"/>
    </svg>

    <h1 class="headline">
      <span class="headline-main">STAY FIT!</span>
      <span class="headline-sub">JOIN US!</span>
    </h1>

    <p class="brand-name">
      <span class="brand-name-main">COPPER RIDGE</span>
      <span class="brand-name-tag">FITNESS</span>
    </p>
  </section>
</body>
</html>
```